Ram and co fleecing works pty ltd

We are sheep shearing contractors,we are looking for a simple design business card, with a drawing like picture of a Australian sheep on it, then just standard details, name, phone, email, po box.
We would like double sided, with 2 lines of wiriting on the back, no bright colours please.
We like black and white, doesn't have to be too serious, however nothing to far left of cwntre.
On the back of the card we would like professional shearing contract offering full contract team.
Can use use the symbol & in the name instead of and.

Target Market(s)

Sheep farmers, target males from age 20 and up

Contact Information for Business Card

Company name ram and co fleecing works pty ltd
Marcus haldenby 0471305846, po box 4072 sale vic 3853,
Email ramandcofleecing@mailbarn.example, gippsland shearing contractor

Font styles to use
Serif

Colors

Designer to choose only greyscale colors for use in the design.

Requirements
Nice to have
• Simple design

```html
<!DOCTYPE html>
<html lang="en">
<head>
<meta charset="utf-8">
<title>Ram &amp; Co Fleecing Works — Business Card</title>
<link href="https://fonts.googleapis.com/css2?family=Arimo:wght@400;700&family=Archivo:wght@800&display=swap" rel="stylesheet">
<style>
  :root {
    --ink: #1c1b19;
    --paper: #ffffff;
    --backdrop: #a3a3a3;
    --rule: #3a3a3a;
    --rule-soft: #8a8a8a;
    --art-dark: #1c1b19;
    --art-mid: #3b3a37;
  }
  * { box-sizing: border-box; margin: 0; padding: 0; }
  html, body { width: 1200px; height: 1200px; overflow: hidden; }
  body {
    background: var(--backdrop);
    font-family: "Arimo", Arial, sans-serif;
    position: relative;
  }
  .card {
    position: absolute;
    top: 303px;
    height: 593px;
    background: var(--paper);
    overflow: hidden;
  }
  .card--back { left: 201px; width: 369px; }
  .card--front { left: 600px; width: 364px; }

  /* Back side */
  .back-header {
    position: absolute; left: 0; top: 0; width: 100%; height: 210px;
    background: var(--ink);
  }
  .brand {
    position: absolute; left: 49px; top: 56px;
    display: flex; align-items: center; gap: 12px;
  }
  .brand-mark {
    width: 70px; height: 76px; border-radius: 6px; background: var(--paper);
    flex: none;
  }
  .brand-name {
    color: var(--paper); font-weight: 400; font-size: 14px; line-height: 1.3;
    letter-spacing: 0.3px; text-transform: uppercase; width: 190px;
  }
  .region {
    position: absolute; left: 0; top: 147px; width: 100%;
    text-align: center; color: var(--paper); font-size: 15px; letter-spacing: 0.2px;
  }
  .note-line {
    position: absolute; left: 42px; width: 275px; height: 1px; background: var(--rule);
  }
  .note-line--1 { top: 295px; }
  .note-line--2 { top: 373px; }
  .note-line--3 { top: 450px; }
  .back-footer {
    position: absolute; left: 0; top: 522px; width: 100%; height: 71px;
    background: var(--ink); color: var(--paper);
    text-align: center; font-size: 16.5px; line-height: 22px; padding-top: 13px;
  }

  /* Front side */
  .front-band {
    position: absolute; left: 0; top: 317px; width: 100%; height: 276px;
    background: var(--ink);
  }
  .sheep-art {
    position: absolute; left: 17px; top: 68px; width: 329px; height: 290px;
    background: linear-gradient(180deg, var(--art-mid), var(--art-dark));
    border-radius: 40px 60px 10px 10px;
  }
  .contact {
    position: absolute; left: 0; top: 398px; width: 100%;
    text-align: center; color: var(--paper);
  }
  .contact-name {
    font-family: "Archivo", "Arial Black", sans-serif; font-weight: 800;
    font-size: 19px; letter-spacing: 0.6px; text-transform: uppercase;
  }
  .divider {
    width: 105px; height: 1px; background: var(--rule-soft); margin: 0 auto;
  }
  .divider--top { margin-top: 12px; margin-bottom: 14px; }
  .divider--bottom { margin-top: 14px; margin-bottom: 10px; }
  .contact-line { font-size: 16px; line-height: 22px; }
</style>
</head>
<body>
  <section class="card card--back" aria-label="Card back">
    <header class="back-header">
      <div class="brand">
        <span class="brand-mark" aria-hidden="true"></span>
        <span class="brand-name">Ram &amp; Co Fleecing Works Pty Ltd</span>
      </div>
      <p class="region">GIPPSLAND SHEARING CONTRACTOR</p>
    </header>
    <span class="note-line note-line--1"></span>
    <span class="note-line note-line--2"></span>
    <span class="note-line note-line--3"></span>
    <footer class="back-footer">
      <p>Professional shearing contract</p>
      <p>offering full contract team</p>
    </footer>
  </section>

  <section class="card card--front" aria-label="Card front">
    <div class="front-band"></div>
    <div class="sheep-art" role="img" aria-label="Black silhouette illustration of a standing horned goat, facing right"></div>
    <div class="contact">
      <p class="contact-name">Marcus Haldenby</p>
      <div class="divider divider--top"></div>
      <p class="contact-line">0471305846</p>
      <p class="contact-line">ramandcofleecing@mailbarn.example</p>
      <div class="divider divider--bottom"></div>
      <p class="contact-line">PO box 4072 sale vic 3853</p>
    </div>
  </section>
</body>
</html>
```